Postcard designed to acquire new customers

Need a postcard style AD to place in dentist offices and other professionals to promote our tax saving system. We will place these in dentists offices, orthodontist, optometrist, physiotherapist and all sorts of medical/dental offices. The card should highlight how they can save taxes by using our software. Our website has good information on it, and I'll include the advertising PDF that our software company produces. Our logo is a little out-dated and I've included the bonus of the winner re-making the logo so its better than it currently is.
Updates

I don't need to have any space allocated for a stamp and address. We are using this to place in offices and are for advertising purposes, not mailing. Thanks!

Reason: My apologies for not providing feedback yet, I've lost several days due to some illness and am finally back at work. I'll be going through designs today and would like the extra few days to work with many of you to create a great design. Thank you for your patience! Dorian

Reason: Again, my apologies for the delay. I will be in contact with designers this week. Thank you,

Target Market(s)

Small Business Owners in Canada

Industry/Entity Type

Health Insurance

Logo Text

Save Time, Save Money

Font styles to use
Other font styles liked:
• Easy to Read Font's

Colors

Designer to choose colors to be used in the design.

Requirements
Must have
• Must have a call to action on the postcard to sell the service. We need people to have their attention caught. A call to action could be, "You're spending too much on taxes! That's what they'll say if your business doesn't have a Birchline Health Spending Account..."
• See the PDF for other catch phrases or key information on what a Health Spending Account is. Many people don't know so I'd like to see 3-4 bullet points on the front of the postcard on what a health spending account is. See the attached PDF for that information and simplifying the information to short bullet points would be best. Here are my thoughts:
• Who should have a Birchline Health Spending Account?
• - Every business owner who is incorporated should have one.
• - Write off 100% of this NFB approved this method.
• - It is the most tax effective way to run dental, health, vision and other expenses through your company.
• - Easy to use APP for your phone, 2-day turnaround time for claims
• If you aren't using this, you're throwing tax dollars away!
• The back of the postcard would include 2 things. First, an example of the taxes you can save, and second - the different information they can send us so we can setup your account.
• First is the example of how this saves you money. Assuming a 38% personal tax rate. You will need to earn $1.62 of gross income, pay $0.62 of personal tax, which leaves you with $1.00 of after tax money to use for your personal expenses.
• The example of using a Birchline Health Spending Account, or doing nothing would need the following information.
• Comparison
• $5,000 of medical, dental, vision expenses
• Do Nothing Birchline Health Spending Account
• $8,100 – Total Cost $5,525 – Total Cost
• $3,100 – Income Tax $500 fee & $25 GST
• $5,000 – Money needed for medical, dental, vision, etc. $5,000 – Money needed for medical, dental, vision, etc.
• SAVINGS is $2,575
• Assuming a company incorporated in Alberta and a one time setup fee of $275 has not been included in the comparison.
• Information to send us to setup your account is:
• - Names and birth dates of you and your dependents
• - Contact information for you and your business (if different) Address, email, phone numbers
• - We will contact you about how to setup the app, your banking details and some other items.
• - Setup fee is a one-time payment of $275
Nice to have
• I'd like the front of the postcard to not be very busy with the background or graphics, etc. I want the call to action to be very obvious so they want to read the bullet points and look at the back of the postcard for more information.

```html
<!DOCTYPE html>
<html lang="en">
<head>
<meta charset="utf-8">
<title>Birchline Health Spending – Postcard</title>
<link href="https://fonts.googleapis.com/css2?family=Montserrat:wght@700;800&family=Open+Sans:ital,wght@0,400;0,600;0,700;1,400&display=swap" rel="stylesheet">
<style>
  :root {
    --stage: #2a2a2a;
    --red: #e31b23;
    --blue: #1a74bb;
    --ink: #1c1c1c;
    --pink-band: #fde6e6;
    --sky: #cfe5f5;
    --rule: #c9cdd2;
  }
  * { box-sizing: border-box; margin: 0; padding: 0; }
  html, body { width: 900px; height: 1200px; overflow: hidden; background: var(--stage); }
  body { position: relative; font-family: "Open Sans", Arial, sans-serif; color: var(--ink); }

  .card {
    position: absolute; left: 126px; width: 648px; height: 459px;
    background: linear-gradient(to bottom, #ffffff 0%, #ffffff 35%, var(--sky) 100%);
    overflow: hidden;
  }
  .card--back { top: 75px; }
  .card--front { top: 562px; }
  .abs { position: absolute; }

  .brand { display: flex; align-items: flex-start; gap: 10px; }
  .brand__mark { width: 40px; height: 40px; background: var(--red); flex: none; margin-top: 2px; }
  .brand__name { font-weight: 600; color: var(--red); line-height: 1.1; white-space: nowrap; }
  .brand__tagline { font-style: italic; color: var(--ink); line-height: 1.2; margin-top: 2px; }

  .header-band { left: 0; top: 22px; width: 648px; height: 76px; background: var(--pink-band); }

  .section-title {
    font-family: "Montserrat", Arial, sans-serif; font-weight: 800; color: var(--red);
    font-size: 16px; line-height: 16px; text-transform: uppercase; letter-spacing: -0.2px;
  }
  .body-copy { font-size: 9.6px; line-height: 12.6px; letter-spacing: -0.2px; }
  .divider { width: 2px; background: #ef8a8a; }

  .compare-title { font-family: "Open Sans", Arial, sans-serif; font-weight: 700; color: var(--blue); font-size: 14px; text-align: center; }
  .compare-sub { font-size: 9.6px; text-align: center; }
  .compare-table { border-collapse: collapse; width: 273px; font-size: 9.6px; line-height: 12.4px; letter-spacing: -0.2px; }
  .compare-table th { background: var(--red); color: #fff; font-weight: 700; text-align: left; padding: 6px 7px; height: 32px; width: 50%; vertical-align: middle; line-height: 11px; }
  .compare-table td { vertical-align: top; padding: 3px 7px; }
  .compare-table .total td { border-top: 1.5px solid var(--ink); padding-top: 2px; }
  .savings { color: var(--red); font-size: 13px; font-weight: 600; text-align: center; }

  .bullets { list-style: none; }
  .bullets li { position: relative; padding-left: 8px; }
  .bullets li::before { content: "•"; position: absolute; left: 0; }

  .photo-slot { background: linear-gradient(135deg, #5b5b5b 0%, #8a8a8a 45%, #6b5a48 100%); }
  .illustration-slot { background: radial-gradient(ellipse at 60% 55%, #d8d8d8 0%, #9b9b9b 55%, rgba(155,155,155,0) 75%); }

  .who-title { font-weight: 700; color: var(--blue); font-size: 14px; line-height: 17px; }
  .who-list { font-size: 11.2px; line-height: 13.6px; letter-spacing: -0.1px; }
  .who-list li { margin-bottom: 5px; }

  .stamp-box { border: 2px solid #555; background: #fff; }
  .address-line { height: 1.5px; background: var(--rule); }

  .cta-band { left: 0; top: 329px; width: 648px; height: 53px; background: var(--red); }
  .cta-headline {
    font-family: "Montserrat", Arial, sans-serif; font-weight: 800; color: #fff;
    font-size: 22px; line-height: 24px; text-transform: uppercase; letter-spacing: -0.3px;
  }
  .cta-sub { color: var(--red); font-size: 12.4px; line-height: 15px; letter-spacing: -0.3px; }
  .cta-closing {
    font-family: "Montserrat", Arial, sans-serif; font-weight: 800; color: var(--blue);
    font-size: 12.4px; line-height: 14px; text-transform: uppercase; text-align: center;
  }
</style>
</head>
<body>

  <!-- Back side: savings example and account setup -->
  <section class="card card--back">
    <div class="abs header-band"></div>
    <div class="abs brand" style="left:150px; top:34px;">
      <div class="brand__mark"></div>
      <div>
        <div class="brand__name" style="font-size:22px;">Birchline Health Spending</div>
        <div class="brand__tagline" style="font-size:14px; margin-left:38px;">Save Time - Save Money</div>
      </div>
    </div>

    <h2 class="abs section-title" style="left:27px; top:108px;">The example of<br>how this saves you money.</h2>
    <div class="abs body-copy" style="left:27px; top:150px; width:280px;">
      <p>Assuming a 38% personal tax rate. You will need to earn $1.62 of gross income, pay $0.62 of personal tax, which leaves you with $1.00 of after tax money to use for your personal expenses.</p>
      <p>The example of usig a Birchline Health Spending Account, or doing nothing would need the following information.</p>
    </div>

    <div class="abs" style="left:27px; top:233px; width:273px;">
      <div class="compare-title">COMPARISON</div>
      <div class="compare-sub" style="margin-bottom:4px;">$5,000 of medical, dental, vision expenses</div>
      <table class="compare-table">
        <tr><th>Do Nothing</th><th>Birchline Health Spending Account</th></tr>
        <tr>
          <td>$3,100 – Income Tax<br>$5,000 – Money needed for medical, dental, vision, etc.</td>
          <td>$500 fee &amp; $25 GST<br>$5,000 – Money needed for medical, dental, vision, etc.</td>
        </tr>
        <tr class="total"><td>$8,100 – Total Cost</td><td>$5,525 – Total Cost</td></tr>
      </table>
      <div class="savings" style="margin-top:3px;">SAVINGS is $2,575</div>
      <p class="body-copy" style="margin-top:2px;">Assuming a company incorporated in Alberta and a one time setup fee of $275 has not been included in the comparison.</p>
    </div>

    <div class="abs divider" style="left:323px; top:106px; height:324px;"></div>

    <h2 class="abs section-title" style="left:347px; top:108px;">Information to send us to<br>setup your account is:</h2>
    <ul class="abs bullets body-copy" style="left:347px; top:148px; width:280px; line-height:12px;">
      <li>Names and birth dates of you and your dependents</li>
      <li>Contact information for you and your business (if different) Address, email, phone numbers</li>
      <li>We will contact you about how to setup the app, your banking details and some other items.</li>
      <li>Setup fee is a one-time payment of $275</li>
    </ul>

    <div class="abs photo-slot" role="img" aria-label="Photo of a hand dropping a coin into a white piggy bank beside stacks of coins" style="left:348px; top:230px; width:277px; height:202px;"></div>
  </section>

  <!-- Front side: who should have an account and call to action -->
  <section class="card card--front">
    <div class="abs brand" style="left:30px; top:30px;">
      <div class="brand__mark" style="width:34px; height:34px;"></div>
      <div>
        <div class="brand__name" style="font-size:18px;">Birchline Health Spending</div>
        <div class="brand__tagline" style="font-size:13px; margin-left:40px;">Save Time - Save Money</div>
      </div>
    </div>

    <h2 class="abs who-title" style="left:28px; top:102px;">Who should have a<br>Birchline Health Spending Account?</h2>
    <ul class="abs bullets who-list" style="left:28px; top:139px; width:270px;">
      <li>Every business owner who is incorporated should have one.</li>
      <li>Write off 100% of this NFB approved this method.</li>
      <li>It is the most tax effective way to run dental, health, vision and other expenses through your company.</li>
      <li>Easy to use APP for your phone, 2-day turnaround time for claims</li>
    </ul>

    <div class="abs divider" style="left:323px; top:27px; height:302px;"></div>
    <div class="abs divider" style="left:323px; top:382px; height:48px;"></div>

    <div class="abs stamp-box" style="left:524px; top:26px; width:98px; height:102px;"></div>
    <div class="abs address-line" style="left:351px; top:150px; width:270px;"></div>
    <div class="abs address-line" style="left:351px; top:181px; width:270px;"></div>
    <div class="abs address-line" style="left:351px; top:211px; width:270px;"></div>

    <div class="abs cta-band"></div>
    <div class="abs illustration-slot" role="img" aria-label="Toy figure of an accountant sitting at an office desk with a computer" style="left:386px; top:246px; width:212px; height:128px;"></div>
    <h1 class="abs cta-headline" style="left:26px; top:332px;">You're spending<br>too much on taxes!</h1>

    <p class="abs cta-sub" style="left:29px; top:392px; width:290px;">That's what they'll say if your business doesn't have a Birchline Health Spending Account...</p>
    <p class="abs cta-closing" style="left:334px; top:396px; width:310px;">If you aren't using this,<br>you're throwing tax dollars away!</p>
  </section>

</body>
</html>
```